Front and content page design for Fitness Cookbook

I am looking for someone to Design a front cover for a Recipe book and also create an amazing layout for the book.

Its for a corporate seminar so has to be eye catching, professional and bold.

Content is complete

Target Market(s)

Industry/Entity Type

Health And Wellness

Font styles to use
Sans Serif

Requirements
Must have
• Eye catching, professional and bold.
• By Dorian as stated on the document
• Must have Tidewell Motion Logo on it.

```html
<!DOCTYPE html>
<html lang="en">
<head>
<meta charset="utf-8">
<title>Post Workout Pizza</title>
<link href="https://fonts.googleapis.com/css2?family=Open+Sans:wght@400;600;700&display=swap" rel="stylesheet">
<style>
  :root {
    --orange: #ee7f1f;
    --ink: #2b2b2b;
    --paper: #ffffff;
    --photo-top: #9a8f82;
    --photo-bottom: #7d7266;
    --brand: #3d6f9e;
  }
  * { margin: 0; padding: 0; box-sizing: border-box; }
  html, body { width: 849px; height: 1200px; overflow: hidden; background: var(--paper); }
  body { font-family: "Open Sans", Arial, sans-serif; color: var(--ink); }
  .page { position: relative; width: 849px; height: 1200px; background: var(--paper); }

  .hero-photo {
    position: absolute; left: 0; top: 0; width: 849px; height: 509px;
    background: linear-gradient(180deg, var(--photo-top) 0%, var(--photo-bottom) 100%);
  }

  .title-band {
    position: absolute; left: 0; top: 509px; width: 849px; height: 156px;
    background: var(--orange);
    display: flex; align-items: center; justify-content: center;
  }
  .title-band h1 {
    color: var(--paper); font-weight: 400; font-size: 50px; letter-spacing: 0.3px;
  }

  .recipe {
    position: absolute; left: 54px; top: 692px; width: 730px;
    font-size: 14.5px; line-height: 17.5px;
  }
  .label { color: var(--orange); font-weight: 700; text-transform: uppercase; letter-spacing: 0.3px; }
  .section-head { font-size: 14.5px; line-height: 17.5px; }
  .ingredients-head { margin-top: 27px; }
  .method-head { margin-top: 34px; }
  .ingredients { list-style: none; }

  .footer-brand {
    position: absolute; right: 40px; bottom: 10px;
    display: flex; align-items: center; gap: 6px;
    font-size: 11px; color: var(--brand); font-weight: 600;
  }
  .footer-brand .mark { width: 10px; height: 10px; background: var(--brand); }
  .footer-brand .page-number { color: var(--ink); font-weight: 400; margin-left: 14px; font-size: 12px; }
</style>
</head>
<body>
<div class="page">
  <div class="hero-photo" role="img" aria-label="Photo of a wholewheat wrap pizza topped with chicken, broccoli, asparagus, tomato slices and pesto"></div>

  <header class="title-band">
    <h1>Post Workout Pizza</h1>
  </header>

  <section class="recipe">
    <div class="timing">
      <p><span class="label">Prep time</span> 5 mins</p>
      <p><span class="label">Cooking time</span> 30 mins</p>
    </div>

    <h2 class="label section-head ingredients-head">Ingredients</h2>
    <ul class="ingredients">
      <li>200g chicken breast</li>
      <li>1 whole wheat wrap</li>
      <li>3 tbsp green pesto</li>
      <li>1/2 cup broccoli florets (cut very small)</li>
      <li>1/2 cup asparagus (cut small)</li>
      <li>1 plum tomato (thinly sliced)</li>
      <li>1/2 cup mature cheddar cheese (optional)</li>
    </ul>

    <h2 class="label section-head method-head">Cooking Instructions</h2>
    <p class="method">Bake the chicken at 190°C/374°F for 18-20 mins until cooked. Cut up into pieces and mix in a bowl with the broccoli and asparagus. Lay the wrap on a baking tray and spread the pesto on top leaving an inch around the edges for the crust. Place the other ingredients on top including the sliced tomato. Put back into the oven for 10 mins, cut into slices and serve.</p>
  </section>

  <footer class="footer-brand">
    <span class="mark"></span>
    <span class="brand-name">Tidewell Motion</span>
    <span class="page-number">15</span>
  </footer>
</div>
</body>
</html>
```